Tavenridge Air Business Card Design

Design new, 2 sides, business cards for a residential and light commercial heating, air conditioning contractor.

Target Market(s)

Homeowners, small businesses

Industry/Entity Type

Business

Contact Information for Business Card

Dominic Westerhall
Phone - 862-415-2736
Email
Address - PO box 518
Brightwater NJ 07912
Website - www.TavenridgeAirLLC.example

Requirements
Must have
• logo, company colors, standard size with no die cut, so I can use nova stamp

```html
<!DOCTYPE html>
<html lang="en">
<head>
<meta charset="utf-8">
<title>Tavenridge Air Business Card</title>
<link rel="stylesheet" href="https://fonts.googleapis.com/css2?family=Barlow+Semi+Condensed:wght@400;500;600;700&family=Roboto:wght@400&display=swap">
<style>
  :root {
    --backdrop: #ececec;
    --card-maroon: #8b2b26;
    --accent-yellow: #e5b60a;
    --name-yellow: #f6c417;
    --wordmark-cream: #f4e2b0;
    --mark-orange: #e98a1e;
    --text-light: #f5efe6;
    --text-dark: #3a1410;
  }
  * { margin: 0; padding: 0; box-sizing: border-box; }
  html, body {
    width: 1200px; height: 576px; overflow: hidden;
    background: var(--backdrop);
  }
  .stage { position: relative; width: 1200px; height: 576px; }
  .card {
    position: absolute; top: 138px;
    width: 484px; height: 292px;
    background: var(--card-maroon);
    overflow: hidden;
  }
  .card--front { left: 81px; }
  .card--back { left: 602px; }

  .wordmark {
    position: absolute;
    display: flex; align-items: center; gap: 10px;
    font-family: "Barlow Semi Condensed", sans-serif;
    font-weight: 600;
    color: var(--wordmark-cream);
    white-space: nowrap;
  }
  .wordmark__dot {
    flex: none; border-radius: 50%;
    background: var(--mark-orange);
  }
  .card--front .wordmark {
    left: 50%; top: 134px; transform: translate(-50%, -50%);
    font-size: 44px;
  }
  .card--front .wordmark__dot { width: 22px; height: 22px; }
  .card--back .wordmark {
    left: 130px; top: 142px; transform: translate(-50%, -50%);
    font-size: 28px; gap: 8px;
  }
  .card--back .wordmark__dot { width: 14px; height: 14px; }

  .service-band {
    position: absolute; left: 0; right: 0; top: 249px; height: 22px;
    background: var(--accent-yellow);
    font-family: "Roboto", sans-serif; font-size: 12px;
    color: var(--text-dark);
    display: flex; align-items: center; justify-content: center;
    gap: 6px;
  }

  .contact-block {
    position: absolute; left: 254px; top: 80px;
    font-family: "Barlow Semi Condensed", sans-serif;
    color: var(--text-light);
  }
  .contact-block__name {
    font-weight: 700; font-size: 16px; color: var(--name-yellow);
    line-height: 20px;
  }
  .contact-block__title {
    font-size: 11px; line-height: 14px; margin-top: 2px;
  }
  .contact-list { list-style: none; margin-top: 22px; }
  .contact-list__item {
    display: flex; align-items: center;
    height: 17px; font-size: 12px; letter-spacing: 0.1px;
    white-space: nowrap;
  }
  .contact-list__icon {
    width: 11px; height: 11px; margin-left: 3px; margin-right: 10px;
    fill: var(--name-yellow); flex: none;
  }
  .bottom-stripe {
    position: absolute; left: 0; right: 0; bottom: 0; height: 7px;
    background: var(--accent-yellow);
  }
</style>
</head>
<body>
<main class="stage">
  <section class="card card--front" aria-label="Card front">
    <div class="wordmark"><span class="wordmark__dot"></span>Tavenridge Air</div>
    <div class="service-band">
      <span>Residential &amp; Light Commercial Heating</span>
      <span>•</span>
      <span>Air Conditioning Contractor</span>
    </div>
  </section>

  <section class="card card--back" aria-label="Card back">
    <div class="wordmark"><span class="wordmark__dot"></span>Tavenridge Air</div>
    <div class="contact-block">
      <p class="contact-block__name">Dominic Westerhall</p>
      <p class="contact-block__title">Managing Director</p>
      <ul class="contact-list">
        <li class="contact-list__item">
          <svg class="contact-list__icon" viewBox="0 0 12 12" aria-hidden="true"><path d="M1 4.5C1 3 3 2 6 2s5 1 5 2.5V5H8.5V4H3.5v1H1z"/><rect x="2.5" y="6" width="7" height="4.5" rx="1"/></svg>
          <span>862-415-2736</span>
        </li>
        <li class="contact-list__item">
          <svg class="contact-list__icon" viewBox="0 0 12 12" aria-hidden="true"><path d="M1 2.5h10v1L6 6.8 1 3.5z"/><path d="M1 4.8l5 3.3 5-3.3v4.7H1z"/></svg>
          <span>info@TavenridgeAirLLC.example</span>
        </li>
        <li class="contact-list__item">
          <svg class="contact-list__icon" viewBox="0 0 12 12" aria-hidden="true"><path fill-rule="evenodd" d="M6 1a5 5 0 110 10A5 5 0 016 1zm0 1.2c-.6.8-1 1.9-1.1 3.2h2.2C7 4.1 6.6 3 6 2.2zM2.3 5.4h1.5c.1-1.1.4-2 .8-2.8a3.9 3.9 0 00-2.3 2.8zm5.9 0h1.5a3.9 3.9 0 00-2.3-2.8c.4.8.7 1.7.8 2.8zM2.3 6.6a3.9 3.9 0 002.3 2.8c-.4-.8-.7-1.700-.8-2.8zm2.6 0c.1 1.3.5 2.4 1.1 3.2.6-.8 1-1.9 1.1-3.2zm3.3 0c-.1 1.1-.4 2-.8 2.8a3.9 3.9 0 002.3-2.8z"/></svg>
          <span>www.TavenridgeAirLLC.example</span>
        </li>
        <li class="contact-list__item">
          <svg class="contact-list__icon" viewBox="0 0 12 12" aria-hidden="true"><path fill-rule="evenodd" d="M6 .8a4 4 0 014 4c0 2.8-4 6.7-4 6.7S2 7.6 2 4.8a4 4 0 014-4zm0 2.4a1.6 1.6 0 100 3.2 1.6 1.6 0 000-3.2z"/></svg>
          <span>PO box 518 Brightwater NJ 07912</span>
        </li>
      </ul>
    </div>
    <div class="bottom-stripe"></div>
  </section>
</main>
</body>
</html>
```